NZ First of it's kind solutions directory and marketplace for busy Mums needs a business card design

We need a business card design for our new nationwide business in NZ (long term plans to go global). We provide solutions to the everyday challenges that busy Mums face by connecting them with quality communities and suppliers of carefully selected, relevant products and services. We sell direct via our online marketplace. The final design should communicate our values of inclusivity, quality and smart solutions. Colours should incorporate our logo colour palette of #477077 and #6ba8b2. Our website is at https://www.brightnestmums.example

Target Market(s)

busy Mums, Age 28 – 50, female, income over $100K, location main centres NZ primarily but NZ wide. Is likely juggling work or career with a young family. Probably had hobbies which have fallen by the wayside.
-Wants to succeed in her chosen career without compromising on family life
-to successfully juggle her career without feeling like she is compromising her children
- Is time poor, something always has to give and it’s generally her health (she’ll stay up late, get stressed)
- probably ex corporate or professional career. Has discretional income

Industry/Entity Type

Business

Contact Information for Business Card

Lena Forbisher, Founder, BrightNestMums.example (Strapline Tap; Gather; Sorted), 47 Kowhai Terrace, Ellerslie, Auckland 1051, New Zealand. Mob: 021 483 517 Ph: +64 (0)9 571 4860

Font styles to use
Other font styles liked:
• Raleway, and/or Architects Daughter

Colors
00a990
33b8a4
86cfc6
cfeae6

Requirements
Must have
• the above details, streamline. the logo and colours associated with those logos
Should not have
• foil or metallic colours

```html
<!DOCTYPE html>
<html lang="en">
<head>
<meta charset="utf-8">
<title>BrightNestMums business card</title>
<link rel="stylesheet" href="https://fonts.googleapis.com/css2?family=Work+Sans:wght@400;500;600;700&display=swap">
<style>
  :root {
    --teal-dark: #477077;
    --teal-light: #6ba8b2;
    --ink: #3f6168;
    --paper: #ffffff;
    --backdrop: #e9ecec;
    --photo-warm: #b38358;
    --photo-cool: #8e9aa6;
  }
  * { box-sizing: border-box; margin: 0; padding: 0; }
  html, body { width: 1200px; height: 930px; overflow: hidden; }
  body {
    background: var(--backdrop);
    font-family: "Work Sans", sans-serif;
    position: relative;
  }
  .card {
    position: absolute;
    width: 640px;
    height: 366px;
    border-radius: 16px;
    overflow: hidden;
    box-shadow: 0 14px 30px rgba(0,0,0,0.18);
  }
  /* Front */
  .card-front { left: 110px; top: 70px; }
  .front-photo {
    position: absolute; inset: 0;
    background:
      radial-gradient(ellipse at 38% 40%, rgba(179,131,88,0.9) 0%, rgba(179,131,88,0.35) 35%, transparent 60%),
      linear-gradient(135deg, #6f7b88 0%, var(--photo-cool) 45%, #c9c3bb 75%, #9aa3ad 100%);
  }
  .front-shade { position: absolute; inset: 0; background: rgba(40,48,56,0.28); }
  .front-brand {
    position: absolute; left: 0; right: 0; top: 150px;
    text-align: center;
    color: var(--paper);
    font-weight: 700;
    font-size: 48px;
    letter-spacing: -1px;
  }
  .front-web {
    position: absolute; left: 0; right: 0; top: 224px;
    text-align: center;
    color: var(--paper);
    font-size: 15px;
    letter-spacing: 0.5px;
  }
  /* Back */
  .card-back { left: 450px; top: 500px; background: var(--paper); }
  .back-brand {
    position: absolute; left: 40px; top: 56px;
    color: var(--teal-dark);
    font-weight: 700;
    font-size: 40px;
    letter-spacing: -1px;
  }
  .person { position: absolute; right: 40px; top: 126px; text-align: right; }
  .person-name { color: var(--ink); font-weight: 600; font-size: 30px; letter-spacing: -0.5px; line-height: 1; }
  .person-role { color: var(--ink); font-size: 15px; margin-top: 4px; }
  .divider {
    position: absolute; left: 40px; right: 40px; top: 196px;
    height: 1px; background: var(--teal-dark);
  }
  .address {
    position: absolute; right: 40px; top: 208px;
    text-align: right; color: var(--ink);
    font-size: 15px; line-height: 1.35; letter-spacing: 0.3px;
    z-index: 1;
  }
  .contacts {
    position: absolute; left: 40px; top: 212px;
    list-style: none; color: var(--ink);
    font-size: 15px; line-height: 1.4; letter-spacing: 0.3px;
    z-index: 1;
  }
  .contacts li { display: flex; align-items: center; gap: 8px; }
  .contacts svg { width: 12px; height: 12px; flex: none; }
  .wave { position: absolute; left: 0; top: 0; width: 640px; height: 366px; }
</style>
</head>
<body>
  <section class="card card-front" aria-label="Card front">
    <div class="front-photo" role="img" aria-label="Photo of a tired mother resting her face in her hands, in warm soft light"></div>
    <div class="front-shade"></div>
    <div class="front-brand">BrightNestMums</div>
    <div class="front-web">www.brightnestmums.example</div>
  </section>

  <section class="card card-back" aria-label="Card back">
    <svg class="wave" viewBox="0 0 640 366" aria-hidden="true">
      <path d="M0 336 C200 340 330 320 420 286 C500 258 560 264 640 262 L640 270 C560 272 505 268 428 294 C340 326 210 348 0 346 Z" fill="var(--teal-light)"/>
      <path d="M0 350 C210 352 345 332 436 300 C515 274 570 276 640 276 L640 366 L0 366 Z" fill="var(--teal-dark)"/>
    </svg>
    <div class="back-brand">BrightNestMums</div>
    <div class="person">
      <div class="person-name">Lena Forbisher</div>
      <div class="person-role">Founder</div>
    </div>
    <div class="divider"></div>
    <ul class="contacts">
      <li>
        <svg viewBox="0 0 12 12"><rect x="3" y="1" width="6" height="10" rx="1.2" fill="none" stroke="var(--teal-dark)" stroke-width="1.2"/></svg>
        021 483 517
      </li>
      <li>
        <svg viewBox="0 0 12 12"><path d="M2.5 1.5 L4.5 1.5 L5.2 4 L4 5 C4.6 6.4 5.6 7.4 7 8 L8 6.8 L10.5 7.5 L10.5 9.5 C10.5 10.2 9.8 10.6 9 10.5 C5 10 2 7 1.5 3 C1.4 2.2 1.8 1.5 2.5 1.5 Z" fill="var(--teal-dark)"/></svg>
        +64 (0)9 571 4860
      </li>
      <li>
        <svg viewBox="0 0 12 12"><circle cx="6" cy="6" r="4.8" fill="none" stroke="var(--teal-dark)" stroke-width="1"/><ellipse cx="6" cy="6" rx="2" ry="4.8" fill="none" stroke="var(--teal-dark)" stroke-width="0.9"/><line x1="1.2" y1="6" x2="10.8" y2="6" stroke="var(--teal-dark)" stroke-width="0.9"/></svg>
        www.brightnestmums.example
      </li>
    </ul>
    <div class="address">
      47 Kowhai Terrace, Ellerslie<br>
      Auckland 1051, New Zealand
    </div>
  </section>
</body>
</html>
```